Road Construction Company needs business cards

We would like a new business card designed for our business.

We're a road construction company based in Qld, Australia.

Can the business card please have the following information on it.

Name: Warren Halbeck
Position: General Manager
Phone: 0472 915 348
Email: Warren.halbeck@tovrin.com.au
Address: 87 Marrow Ave, Pendlebay, QLD, 4023
Website: www.tovrin.com.au

Visually we'd like the card to be professional and simple.

Attached is our logo.

Our website is www.tovrin.com.au

Target Market(s)

Men aged 25-60

Contact Information for Business Card

As listed in project description

Font styles to use
Serif

Requirements
Must have
• Large logo on back of card

```html
<!DOCTYPE html>
<html lang="en">
<head>
<meta charset="utf-8">
<title>Tovrin Business Card</title>
<link href="https://fonts.googleapis.com/css2?family=Inter:wght@400;500;700;800&display=swap" rel="stylesheet">
<style>
  :root {
    --brand-blue: #0b56a4;
    --brand-deep: #1a3a78;
    --brand-sky: #2ea2dc;
    --ink: #505357;
    --paper: #ffffff;
    --backdrop: #9a9a9a;
  }
  * { box-sizing: border-box; margin: 0; padding: 0; }
  html, body { width: 1200px; height: 588px; overflow: hidden; }
  body {
    background: var(--backdrop);
    font-family: "Inter", Arial, sans-serif;
    position: relative;
  }
  .card {
    position: absolute;
    width: 486px;
    height: 287px;
    overflow: hidden;
  }
  .wordmark {
    position: absolute;
    font-family: "Inter", Arial, sans-serif;
    font-weight: 800;
    line-height: 1;
    white-space: nowrap;
  }
  .tagline {
    position: absolute;
    font-family: "Inter", Arial, sans-serif;
    font-weight: 700;
    color: var(--brand-sky);
    line-height: 1;
    white-space: nowrap;
  }

  /* Front */
  .card--front {
    left: 87px; top: 141px;
    background: var(--brand-blue);
  }
  .front-bands {
    position: absolute; inset: 0;
    width: 486px; height: 287px;
  }
  .card--front .wordmark {
    left: 98px; top: 252px;
    top: 111px;
    color: var(--paper);
    font-size: 51px;
    letter-spacing: 10px;
  }
  .card--front .tagline {
    left: 99px; top: 162px;
    font-size: 10px;
    letter-spacing: 9.6px;
  }

  /* Back */
  .card--back {
    left: 622px; top: 143px;
    background: var(--paper);
  }
  .card--back .wordmark {
    left: 28px; top: 122px;
    color: var(--brand-blue);
    font-size: 37px;
    letter-spacing: 5px;
  }
  .card--back .tagline {
    left: 29px; top: 156px;
    font-size: 8px;
    letter-spacing: 6.3px;
  }
  .divider {
    position: absolute;
    left: 246px; top: 69px;
    width: 1.5px; height: 150px;
    background: var(--brand-blue);
  }
  .details {
    position: absolute;
    left: 258px; top: 64px;
    color: var(--ink);
  }
  .details__name {
    font-weight: 700;
    font-size: 19px;
    color: var(--brand-blue);
    line-height: 1.1;
  }
  .details__title {
    font-size: 14px;
    color: var(--brand-sky);
    margin-top: 1px;
  }
  .details__address {
    font-size: 13.5px;
    line-height: 18px;
    margin-top: 12px;
  }
  .contact {
    list-style: none;
    margin-top: 14px;
    font-size: 13.5px;
    line-height: 18px;
  }
  .contact li { display: flex; align-items: center; gap: 5px; }
  .contact svg { width: 10px; height: 10px; fill: var(--brand-blue); flex: none; }
</style>
</head>
<body>
  <section class="card card--front" aria-label="Card front">
    <svg class="front-bands" viewBox="0 0 486 287" aria-hidden="true">
      <defs>
        <linearGradient id="shade" x1="0" y1="0" x2="1" y2="1">
          <stop offset="0" stop-color="#1a3a78" stop-opacity="0.9"/>
          <stop offset="1" stop-color="#0b56a4" stop-opacity="0"/>
        </linearGradient>
      </defs>
      <polygon points="160,0 486,0 486,287 10,287" fill="url(#shade)" opacity="0.55"/>
      <polygon points="160,0 250,0 110,287 20,287" fill="#1a3a78" opacity="0.35"/>
      <polygon points="330,0 400,0 560,287 450,287" fill="#ffffff" opacity="0.12"/>
      <polygon points="250,0 300,0 420,287 370,287" fill="#ffffff" opacity="0.06"/>
    </svg>
    <div class="wordmark">TOVRIN</div>
    <div class="tagline">ROAD CONSTRUCTION</div>
  </section>

  <section class="card card--back" aria-label="Card back">
    <div class="wordmark">TOVRIN</div>
    <div class="tagline">ROAD CONSTRUCTION</div>
    <div class="divider"></div>
    <div class="details">
      <h1 class="details__name">WARREN HALBECK</h1>
      <p class="details__title">General Manager</p>
      <p class="details__address">87 Marrow Ave<br>Pendlebay, QLD, 4023</p>
      <ul class="contact">
        <li>
          <svg viewBox="0 0 24 24" aria-hidden="true"><path d="M6.6 10.8a15.1 15.1 0 0 0 6.6 6.6l2.2-2.2a1 1 0 0 1 1-.25 11.4 11.4 0 0 0 3.6.57 1 1 0 0 1 1 1V20a1 1 0 0 1-1 1A17 17 0 0 1 3 4a1 1 0 0 1 1-1h3.5a1 1 0 0 1 1 1c0 1.25.2 2.45.57 3.57a1 1 0 0 1-.25 1z"/></svg>
          0472 915 348
        </li>
        <li>
          <svg viewBox="0 0 24 24" aria-hidden="true"><path d="M2 5h20v2l-10 6L2 7z M2 9l10 6 10-6v10H2z"/></svg>
          Warren.halbeck@tovrin.com.au
        </li>
        <li>
          <svg viewBox="0 0 24 24" aria-hidden="true"><circle cx="12" cy="12" r="10"/><path d="M2 12h20M12 2c3 3 3 17 0 20M12 2c-3 3-3 17 0 20" stroke="#fff" stroke-width="1.6" fill="none"/></svg>
          www.tovrin.com.au
        </li>
      </ul>
    </div>
  </section>
</body>
</html>
```